Corvane Capital Business Cards

These are professional business cards that are for my family office.
Put fake emails and phone numbers as of now until I finalize those components. This family office controls my families investments, assets, and future. The cards should be professional.
..
.
.
.
I just uploaded another variation of a logo I would like to see as a business card to I am inbeteen which logo to use

Target Market(s)

business

Industry/Entity Type

business

Contact Information for Business Card

Professional, wealth related, finance related.

Requirements
Must have
• Logo

```html
<!DOCTYPE html>
<html lang="en">
<head>
<meta charset="UTF-8">
<title>Corvane Capital Business Cards</title>
<link href="https://fonts.googleapis.com/css2?family=Playfair+Display:wght@400&family=Poppins:wght@400&display=swap" rel="stylesheet">
<style>
  :root {
    --backdrop: #1f1f1f;
    --card: #0b0b0b;
    --card-edge: #c9b27a;
    --gold: #c6ad72;
    --white: #f4f4f4;
    --silver: #c9c9c9;
    --divider: #5a5a5a;
  }
  * { margin: 0; padding: 0; box-sizing: border-box; }
  html, body {
    width: 1200px; height: 900px; overflow: hidden;
    background: var(--backdrop);
  }
  .sheet {
    width: 1200px; height: 900px;
    display: flex; flex-direction: column;
    align-items: center; justify-content: center; gap: 56px;
  }
  .card {
    width: 660px; height: 377px;
    background: radial-gradient(ellipse at 40% 30%, #171717 0%, var(--card) 70%);
    border-radius: 24px;
    border-bottom: 5px solid var(--card-edge);
    position: relative;
    overflow: hidden;
  }
  .card--front { display: flex; align-items: center; }
  .brand-block {
    width: 330px; height: 100%;
    padding: 0 28px;
    display: flex; align-items: center; justify-content: center;
  }
  .wordmark {
    font-family: "Playfair Display", serif;
    font-weight: 400;
    text-transform: uppercase;
    letter-spacing: 2px;
    white-space: nowrap;
    display: flex; align-items: center; gap: 12px;
  }
  .wordmark__square {
    width: 11px; height: 11px; background: currentColor; flex: none;
  }
  .card--front .wordmark { color: var(--white); font-size: 25px; }
  .divider {
    width: 1px; height: 250px; flex: none;
    background: linear-gradient(to bottom, transparent, var(--divider), transparent);
  }
  .contact-block {
    padding-left: 36px;
    font-family: "Poppins", sans-serif;
    font-weight: 400;
    color: var(--white);
  }
  .person-name {
    font-family: "Playfair Display", serif;
    font-weight: 400;
    font-size: 24px; letter-spacing: 1px;
    text-transform: uppercase; line-height: 1;
  }
  .person-name__surname { color: var(--gold); }
  .person-title { font-size: 16px; margin-top: 4px; margin-bottom: 18px; }
  .contact-list { list-style: none; }
  .contact-item {
    display: flex; align-items: center; gap: 10px;
    font-size: 16px; line-height: 1.55;
  }
  .contact-item svg { width: 16px; height: 16px; flex: none; }
  .address { font-size: 16px; line-height: 1.35; margin-top: 16px; }
  .card--back {
    display: flex; align-items: center; justify-content: center;
    border-bottom-width: 7px;
  }
  .card--back .wordmark { color: var(--silver); font-size: 44px; letter-spacing: 3px; }
</style>
</head>
<body>
<main class="sheet">
  <section class="card card--front">
    <div class="brand-block">
      <div class="wordmark"><span class="wordmark__square"></span>Corvane Capital</div>
    </div>
    <div class="divider"></div>
    <div class="contact-block">
      <h1 class="person-name">Daniel <span class="person-name__surname">Hartley</span></h1>
      <p class="person-title">Managing Director</p>
      <ul class="contact-list">
        <li class="contact-item">
          <svg viewBox="0 0 24 24" aria-hidden="true"><path fill="var(--gold)" d="M6.6 10.8a15.1 15.1 0 0 0 6.6 6.6l2.2-2.2a1 1 0 0 1 1-.25 11.4 11.4 0 0 0 3.6.57 1 1 0 0 1 1 1V20a1 1 0 0 1-1 1A17 17 0 0 1 3 4a1 1 0 0 1 1-1h3.5a1 1 0 0 1 1 1c0 1.250.2 2.45.57 3.57a1 1 0 0 1-.25 1z"/></svg>
          044-555 010 274
        </li>
        <li class="contact-item">
          <svg viewBox="0 0 24 24" aria-hidden="true"><path fill="var(--gold)" d="M2 5h20v14H2zm2 2v.4l8 5 8-5V7zm0 2.8V17h16V9.8l-8 5z"/></svg>
          info@corvanemail.com
        </li>
        <li class="contact-item">
          <svg viewBox="0 0 24 24" aria-hidden="true"><g fill="none" stroke="var(--gold)" stroke-width="1.8"><circle cx="12" cy="12" r="9"/><ellipse cx="12" cy="12" rx="4" ry="9"/><path d="M3 12h18M5 7h14M5 17h14"/></g></svg>
          www.corvanesite.com
        </li>
      </ul>
      <p class="address">18 Harrow Lane, Suite 4<br>20190, Eastmoor</p>
    </div>
  </section>

  <section class="card card--back">
    <div class="wordmark"><span class="wordmark__square"></span>Corvane Capital</div>
  </section>
</main>
</body>
</html>
```